Sophisticated, clean website reflecting my feminine, playful side to sell my abstract art,

I need a website no more than 3 pages to showcase my paintings, a little about me and some contact info. I do abstracts so looking for something a little edgy, yet feminine and current.
Updates

Hi there, These are some artists websites that I Iike: Marnelvoss.com (I like how airy it is) peterwallombry.com garethpolvens.com (I like how it scrolls) I'll need a place for a photo ( a headshot-i do not have it yet so I'll need to be able to upload that later) as well as an area for my bio. Also, it's important that I will be able to upload any new photos and descriptions easily so it should be user friendly. Lastly, I like in a sunny place so would like to have this seem upbeat and playful as that is how i like to paint. thanks-I'm trying to upload my photos now -

Target Market(s)

ppl ages 35-70 who want large scale art for their homes

Industry/Entity Type

art

Coding

Coded - Design and coding required

Number of Pages Required

3 page

Colors

Designer to choose colors to be used in the design.

Requirements
Must have
• photos of my art, a place for my bio, be easy to reach me. tasteful-nothing too "in your face" -my clients are pretty high end and organized. They like clean lines
Nice to have
• sophisticated background, muted tones in the back-similar clean font throughout-no cursive
Should not have
• too many dark areas. Too many blocks of color. Too serious.

```html
<!DOCTYPE html>
<html lang="en">
<head>
<meta charset="utf-8">
<title>Harriet Sommer — Abstract Art</title>
<link rel="stylesheet" href="https://fonts.googleapis.com/css2?family=Montserrat:wght@300;400;700&family=Questrial&display=swap">
<style>
  :root {
    --ink: #111111;
    --text: #2b2b2b;
    --muted: #555555;
    --rule: #cfcfcf;
    --frame: #bdbdbd;
    --paper: #ffffff;
    --footer-bg: #f4f4f4;
    --orange: #c0621f;
    --teal: #1f8a86;
    --cream: #e9e1cf;
    --charcoal: #222222;
  }
  * { box-sizing: border-box; margin: 0; padding: 0; }
  html, body { width: 1200px; height: 2884px; overflow: hidden; background: var(--paper); }
  body { position: relative; font-family: "Questrial", "Helvetica Neue", sans-serif; color: var(--text); }
  .abs { position: absolute; }

  /* Header */
  .brand { left: 0; width: 1200px; top: 26px; display: flex; justify-content: center; align-items: center; gap: 16px; }
  .brand-square { width: 44px; height: 44px; background: var(--ink); }
  .brand-name { font-family: "Questrial", sans-serif; font-size: 45px; color: var(--ink); letter-spacing: 1px; line-height: 1; }
  .header-rule { left: 0; top: 100px; width: 1200px; height: 2px; background: #e2e2e2; }

  .nav-link { font-size: 16px; line-height: 20px; color: var(--text); top: 122px; transform: translateX(-50%); white-space: nowrap; letter-spacing: .3px; }
  .nav-active::after { content: ""; position: absolute; left: 1px; right: 1px; top: 25px; height: 2px; background: var(--ink); }
  .social { display: flex; align-items: center; gap: 6px; font-size: 17px; line-height: 20px; color: var(--text); white-space: nowrap; }
  .social-dot { width: 30px; height: 30px; border-radius: 50%; background: var(--ink); flex: none; }

  /* Hero */
  .hero { left: 0; top: 162px; width: 1200px; height: 647px;
    background:
      radial-gradient(ellipse at 12% 18%, #d9d6cf 0 12%, transparent 28%),
      radial-gradient(ellipse at 45% 40%, var(--teal) 0 18%, transparent 40%),
      radial-gradient(ellipse at 22% 40%, var(--orange) 0 18%, transparent 42%),
      radial-gradient(ellipse at 75% 45%, #b8651f 0 20%, transparent 45%),
      radial-gradient(ellipse at 92% 40%, #ece4c8 0 14%, transparent 34%),
      radial-gradient(ellipse at 8% 85%, #2aa29c 0 14%, transparent 34%),
      linear-gradient(160deg, #3a2a1d, #161616 60%, #4b3a2a);
  }
  .thumb { top: 660px; width: 171px; height: 119px; border: 2px solid #f2f2f2; }
  .thumb-green { left: 122px; background: linear-gradient(120deg, #e7f0d6, #4bb04a 45%, #8ccf4a); }
  .thumb-teal { left: 321px; background: linear-gradient(90deg, #e6dcc6 0 22%, #147f7a 30% 70%, #e2d6bd 78%); }
  .thumb-splash { left: 515px; background: linear-gradient(135deg, #1b6f6b, #242424 45%, #c06a24 75%, #ddd3bf); }
  .thumb-violet { left: 709px; background: linear-gradient(135deg, #e6e0d8, #6c4c93 40%, #a58ac0 65%, #e9e3dc); }
  .thumb-rust { left: 903px; background: linear-gradient(135deg, #f0e8e2, #a33a1d 45%, #d9a18f 75%, #f3ece6); }

  /* About */
  .portrait-frame { left: 68px; top: 929px; width: 390px; height: 418px; border: 2px solid var(--frame); background: var(--paper); }
  .portrait { left: 120px; top: 892px; width: 290px; height: 454px; background: linear-gradient(180deg, #d8e3ee, #8fb0cf 55%, #7ea2c4); }
  .section-title { font-family: "Montserrat", sans-serif; font-weight: 400; color: var(--ink); line-height: 1; white-space: nowrap; }
  .title-rule { height: 3px; background: #333333; }
  .about-title { left: 515px; top: 948px; font-size: 49px; }
  .about-rule { left: 519px; top: 1010px; width: 64px; }
  .about-copy { left: 515px; top: 1043px; width: 615px; font-size: 18px; line-height: 27px; color: var(--text); }
  .about-copy p { margin-bottom: 15px; }

  /* Gallery */
  .gallery-title { left: 0; width: 1200px; text-align: center; top: 1528px; font-size: 38px; }
  .gallery-rule { left: 583px; top: 1580px; width: 64px; }
  .slide-frame { left: 232px; top: 1620px; width: 757px; height: 459px; border: 7px solid var(--frame); background: #f2f2f2; }
  .slide { left: 245px; top: 1633px; width: 731px; height: 431px;
    background:
      radial-gradient(ellipse at 30% 60%, #5a3d8a 0 18%, transparent 40%),
      radial-gradient(ellipse at 70% 35%, #7b4e9c 0 16%, transparent 38%),
      radial-gradient(ellipse at 10% 20%, #2c3f8a 0 10%, transparent 30%),
      linear-gradient(135deg, #d9c8b3, #8a6a9e 50%, #c9b3a1);
  }
  .arrow { top: 1818px; width: 34px; height: 66px; }
  .arrow-prev { left: 157px; }
  .arrow-next { left: 1024px; }

  /* Contact */
  .contact-title { left: 0; width: 1200px; text-align: center; top: 2220px; font-size: 49px; }
  .contact-rule { left: 556px; top: 2284px; width: 91px; }
  .contact-intro { left: 0; width: 1200px; text-align: center; top: 2316px; font-size: 19px; line-height: 24px; color: var(--text); }
  .contact-icon { width: 66px; height: 64px; border: 1.5px solid var(--charcoal); display: flex; align-items: center; justify-content: center; }
  .icon-phone { left: 285px; top: 2391px; }
  .icon-mail { left: 564px; top: 2391px; }
  .icon-share { left: 872px; top: 2397px; }
  .contact-item { width: 320px; text-align: center; transform: translateX(-50%); }
  .contact-label { font-size: 18px; line-height: 24px; color: var(--text); }
  .contact-value { font-size: 22px; line-height: 28px; color: var(--ink); margin-top: 4px; }
  .contact-value-small { font-size: 18px; line-height: 24px; color: var(--text); margin-top: 4px; }
  .item-phone { left: 309px; top: 2477px; }
  .item-mail { left: 602px; top: 2471px; }
  .item-share { left: 906px; top: 2471px; }

  /* Footer */
  .footer { left: 0; top: 2705px; width: 1200px; height: 179px; background: var(--footer-bg); }
  .footer-brand { left: 128px; top: 2740px; display: flex; align-items: center; gap: 8px; }
  .footer-square { width: 42px; height: 43px; background: var(--ink); }
  .footer-name { font-family: "Montserrat", sans-serif; font-weight: 700; font-size: 29px; color: var(--ink); white-space: nowrap; }
  .footer-link { top: 2752px; font-size: 17px; line-height: 20px; color: var(--text); transform: translateX(-50%); white-space: nowrap; }
  .footer-social { left: 943px; top: 2745px; }
  .copyright { left: 0; width: 1200px; top: 2829px; text-align: center; font-size: 14px; color: var(--muted); }
</style>
</head>
<body>

<header>
  <div class="abs brand">
    <span class="brand-square"></span>
    <span class="brand-name">HARRIET SOMMER</span>
  </div>
  <div class="abs header-rule"></div>
  <nav>
    <span class="abs nav-link nav-active" style="left:209px">HOME</span>
    <span class="abs nav-link" style="left:388px">ABOUT ME</span>
    <span class="abs nav-link" style="left:580px">GALLERY</span>
    <span class="abs nav-link" style="left:768px">CONTACT</span>
    <span class="abs social" style="left:912px; top:116px"><span class="social-dot"></span>@hsommerart</span>
  </nav>
</header>

<section class="hero-section">
  <div class="abs hero" role="img" aria-label="Large abstract painting with orange, teal, black and cream brushstrokes"></div>
  <div class="abs thumb thumb-green" role="img" aria-label="Green abstract painting thumbnail"></div>
  <div class="abs thumb thumb-teal" role="img" aria-label="Teal and cream abstract painting thumbnail"></div>
  <div class="abs thumb thumb-splash" role="img" aria-label="Teal, black and orange splash painting thumbnail"></div>
  <div class="abs thumb thumb-violet" role="img" aria-label="Violet floral abstract painting thumbnail"></div>
  <div class="abs thumb thumb-rust" role="img" aria-label="Rust red swirling abstract painting thumbnail"></div>
</section>

<section class="about">
  <div class="abs portrait-frame"></div>
  <div class="abs portrait" role="img" aria-label="Headshot of the artist in a denim shirt"></div>
  <h2 class="abs section-title about-title">ABOUT ME</h2>
  <div class="abs title-rule about-rule"></div>
  <div class="abs about-copy">
    <p>Lorem ipsum dolor sit amet, consectetur adipiscing elit, sed do eiusmod tempor incididunt ut labore et dolore magna aliqua. Ut enim ad minim veniam, quis nostrud exercitation</p>
    <p>Duis aute irure dolor in reprehenderit in voluptate velit esse cillum dolore eu fugiat nulla pariatur. Excepteur sint occaecat cupidatat non proident, sunt in culpa qui officia deserunt mollit anim id est laborum</p>
    <p>Sed ut perspiciatis unde pariatur. Excepteur sint occaecat cupidatat non proident, sunt in culpa qui officia deserunt mollit anim id est laborum.Sed ut persmollit anim id est laborum.</p>
  </div>
</section>

<section class="gallery">
  <h2 class="abs section-title gallery-title">PHOTO GALLERY</h2>
  <div class="abs title-rule gallery-rule"></div>
  <div class="abs slide-frame"></div>
  <div class="abs slide" role="img" aria-label="Abstract painting in purple, blue and cream with burst shapes"></div>
  <svg class="abs arrow arrow-prev" viewBox="0 0 34 66"><polyline points="32,2 2,33 32,64" fill="none" stroke="#222" stroke-width="2"/></svg>
  <svg class="abs arrow arrow-next" viewBox="0 0 34 66"><polyline points="2,2 32,33 2,64" fill="none" stroke="#222" stroke-width="2"/></svg>
</section>

<section class="contact">
  <h2 class="abs section-title contact-title">CONTACT US</h2>
  <div class="abs title-rule contact-rule"></div>
  <p class="abs contact-intro">Please get in touch with me on below details.</p>

  <div class="abs contact-icon icon-phone">
    <svg width="30" height="30" viewBox="0 0 24 24" fill="none" stroke="#222" stroke-width="1.2" stroke-linejoin="round"><path d="M5 3h4l2 5-2.5 1.5a11 11 0 0 0 6 6L16 13l5 2v4a2 2 0 0 1-2 2A16 16 0 0 1 3 5a2 2 0 0 1 2-2z"/></svg>
  </div>
  <div class="abs contact-icon icon-mail">
    <svg width="32" height="24" viewBox="0 0 32 24" fill="none" stroke="#222" stroke-width="1.2"><rect x="1" y="1" width="30" height="22"/><polyline points="1,1 16,13 31,1"/><line x1="1" y1="23" x2="12" y2="10"/><line x1="31" y1="23" x2="20" y2="10"/></svg>
  </div>
  <div class="abs contact-icon icon-share">
    <svg width="30" height="30" viewBox="0 0 24 24" fill="none" stroke="#222" stroke-width="1.2"><circle cx="18" cy="5" r="2.5"/><circle cx="6" cy="12" r="2.5"/><circle cx="18" cy="19" r="2.5"/><line x1="8.2" y1="10.8" x2="15.8" y2="6.2"/><line x1="8.2" y1="13.2" x2="15.8" y2="17.8"/></svg>
  </div>

  <div class="abs contact-item item-phone">
    <div class="contact-label">Phone number</div>
    <div class="contact-value">(555) 218 4630</div>
  </div>
  <div class="abs contact-item item-mail">
    <div class="contact-label">Email address</div>
    <div class="contact-value">harrietsommer@info.com</div>
  </div>
  <div class="abs contact-item item-share">
    <div class="contact-label">Follow me on social</div>
    <div class="contact-value-small">@hsommerart</div>
  </div>
</section>

<footer>
  <div class="abs footer"></div>
  <div class="abs footer-brand">
    <span class="footer-square"></span>
    <span class="footer-name">HARRIET SOMMER</span>
  </div>
  <span class="abs footer-link" style="left:540px">ABOUT ME</span>
  <span class="abs footer-link" style="left:686px">GALLERY</span>
  <span class="abs footer-link" style="left:829px">CONTACT</span>
  <span class="abs social footer-social"><span class="social-dot"></span>@hsommerart</span>
  <p class="abs copyright">© 2022 Harriet Sommer &nbsp; All Rights Reserved</p>
</footer>

</body>
</html>
```